Varnik Holdings — Business Card Design Brief
Overview
Design a double-sided business card for Varnik Holdings that highlights our two service arms: Varnik Communications (telecommunications) and Varnik Energy (business energy solutions). The card should feel smart and stand out when handed to clients.

Objectives
Showcase our areas of specialty clearly.
Reflect the overall Varnik / Varnik Holdings brand while acknowledging both arms.
Explore using both logos (Communications + Energy) or one unified logo, depending on the design.

Deliverables
One double-sided business card design (front + back).

Content & Copy
Front (preferred): Logo: Varnik / Varnik Holdings
Descriptor: Business Communications | Business Energy
Back:My contact details and company details
Core products: Business Mobile • Telephony • Internet • Business Energy Solutions

Brand & Visual Direction
We have a group logo currently tailored more toward telecoms, plus a separate Varnik Energy logo.
Please explore layouts that use both logos or just one, whichever works best.
Color: I wouldn't mind seeing an option using our the Blue/Purple gradient from our website (varnik-example.co.uk), but also open to non-gradient approaches and other colours..

Overall look: Smart, modern, and distinctive.
Format & Print Specs
Double-sided business card format. (Use a standard size

Must-Haves
Front: Varnik wording or Varnik Holdings wording with atleast 1 logo also on front “Business Communications | Business Energy.”

Back: Contact + company details and core products.
A design that stands out while remaining professional.

Nice-to-Have Options
A gradient version using our site’s Blue/Purple gradient.
A non-gradient version.
A dual-logo treatment versus a single-logo treatment.

Thanks
Owen

```html
<!DOCTYPE html>
<html lang="en">
<head>
<meta charset="utf-8">
<title>Varnik Holdings – Business Cards</title>
<link rel="stylesheet" href="https://fonts.googleapis.com/css2?family=Arimo:wght@400;700&display=swap">
<style>
  :root {
    --navy: #1c1466;
    --lime: #7dbd0f;
    --green: #45a826;
    --sky: #1aa0dc;
    --blue: #1873d3;
    --paper: #ffffff;
    --backdrop: #e4e4e4;
    --ink-light: #ffffff;
  }
  * { margin: 0; padding: 0; box-sizing: border-box; }
  html, body {
    width: 1200px; height: 1200px; overflow: hidden;
    background: var(--backdrop);
    font-family: "Arimo", Arial, sans-serif;
  }
  .canvas { position: relative; width: 1200px; height: 1200px; }
  .card {
    position: absolute;
    width: 689px; height: 393px;
    background: var(--paper);
    overflow: hidden;
  }
  .card--front { left: 267px; top: 159px; }
  .card--back  { left: 262px; top: 653px; }

  .card__wave { position: absolute; inset: 0; width: 100%; height: 100%; }

  .brand-mark {
    position: absolute; border-radius: 50%;
  }
  .card--front .brand-mark { left: 83px; top: 112px; width: 68px; height: 68px; background: var(--green); }
  .card--back .brand-mark  { left: 292px; top: 93px; width: 102px; height: 102px; background: var(--blue); }

  .brand-name {
    position: absolute; font-weight: 700; color: var(--navy); letter-spacing: 1px; line-height: 1;
  }
  .card--front .brand-name { left: 72px; top: 199px; font-size: 46px; }
  .card--back .brand-name { left: 0; width: 100%; text-align: center; top: 212px; font-size: 54px; }

  .brand-descriptor { position: absolute; line-height: 1; }
  .card--front .brand-descriptor {
    left: 72px; top: 248px; font-size: 15px; letter-spacing: 3.4px; color: var(--green);
  }
  .card--back .brand-descriptor {
    left: 0; width: 100%; text-align: center; top: 284px; font-size: 16px; color: var(--blue);
  }

  .contact {
    position: absolute; right: 47px; top: 0;
    color: var(--ink-light); text-align: right; line-height: 1;
  }
  .contact__name { position: absolute; right: 0; top: 52px; white-space: nowrap; font-size: 27px; font-weight: 700; color: var(--lime); }
  .contact__role { position: absolute; right: 0; top: 81px; font-size: 15px; }
  .contact__address { position: absolute; right: 0; top: 120px; white-space: nowrap; font-size: 16px; line-height: 20.5px; }
  .contact__lines { position: absolute; right: 0; top: 173px; list-style: none; }
  .contact__lines li {
    display: flex; align-items: center; justify-content: flex-end;
    height: 20.7px; font-size: 16px; white-space: nowrap;
  }
  .contact__lines svg { width: 13px; height: 13px; margin-left: 14px; flex: none; fill: var(--lime); }
  .services { position: absolute; right: 0; top: 262px; list-style: none; }
  .services li { height: 21.4px; font-size: 16.5px; white-space: nowrap; display: flex; align-items: center; justify-content: flex-end; }
  .services li::after {
    content: ""; width: 5px; height: 5px; border-radius: 50%; background: var(--ink-light);
    margin-left: 8px; margin-right: -2px;
  }
</style>
</head>
<body>
<main class="canvas">

  <section class="card card--front" aria-label="Business card, contact side">
    <svg class="card__wave" viewBox="0 0 804 459" preserveAspectRatio="none" aria-hidden="true">
      <path d="M440 0 C500 40 470 160 420 260 C382 335 382 405 425 459 L804 459 L804 0 Z" fill="var(--navy)"/>
      <path d="M440 0 C478 30 478 100 452 165" fill="none" stroke="var(--lime)" stroke-width="5"/>
      <path d="M400 285 C370 345 378 415 425 459" fill="none" stroke="var(--sky)" stroke-width="5"/>
    </svg>

    <span class="brand-mark" aria-hidden="true"></span>
    <div class="brand-name">VARNIK</div>
    <div class="brand-descriptor">BUSINESS ENERGY</div>

    <div class="contact">
      <div class="contact__name">DANIEL REEVE</div>
      <div class="contact__role">President</div>
      <div class="contact__address">4120 Alder Court<br>Kestrel Bay, Canada 58213</div>
      <ul class="contact__lines">
        <li>555-014-2273
          <svg viewBox="0 0 16 16" aria-hidden="true"><path d="M3.5 1 6 1.5 7 5 5.3 6.3c.8 1.8 2.3 3.3 4.4 4.4L11 9l3.5 1 .5 2.5C14 14.5 12.5 15 11 15 5 14 2 11 1 5 1 3.5 1.5 2 3.5 1Z"/></svg>
        </li>
        <li>555-019-6481
          <svg viewBox="0 0 16 16" aria-hidden="true"><path d="M4 0h8a1 1 0 0 1 1 1v14a1 1 0 0 1-1 1H4a1 1 0 0 1-1-1V1a1 1 0 0 1 1-1Zm1 2v10h6V2Zm3 11a1 1 0 1 0 0 2 1 1 0 0 0 0-2Z"/></svg>
        </li>
        <li>info@VARNIK-EXAMPLE.com
          <svg viewBox="0 0 16 16" aria-hidden="true"><path d="M1 3h14v10H1Zm1.5 1.5L8 9l5.5-4.5Z"/></svg>
        </li>
        <li>www.VARNIK-EXAMPLE.com
          <svg viewBox="0 0 16 16" aria-hidden="true"><circle cx="8" cy="8" r="7"/></svg>
        </li>
      </ul>
      <ul class="services">
        <li>Business Mobile</li>
        <li>Telephony</li>
        <li>Internet</li>
        <li>Business Energy Solutions</li>
      </ul>
    </div>
  </section>

  <section class="card card--back" aria-label="Business card, brand side">
    <span class="brand-mark" aria-hidden="true"></span>
    <div class="brand-name">VARNIK</div>
    <div class="brand-descriptor">BUSINESS COMMUNICATIONS</div>
  </section>

</main>
</body>
</html>
```